Accountability Project Graphics

I want to create 10 social media graphics (new Instagram size 4:5 (1080 x 1350 pixels) focusing on our Quilvo Accountability App, using any of the 3 pictures attached. Use the attached pics only, NO RANDOM STOCK PHOTOGRAPHY. For the color scheme, use the landing page colors/fonts (attached).
You can add any of the 3 photos attached but I mainly need BOLD text that includes these headlines and sub-headlines on them.
Please NOTE for all the headlines below, also add this sub-headline on each graphic:
Stay Consistent with RT in Your Pocket!
Here are the headlines:
• Stop Starting Over Every Monday
• You don't need more willpower. You need more support
• Built for women who are tired of doing this alone
• When Motivation Fades, RT Checks In
• The Support System You've Been Missing
• Support When Motivation Disappears
• What if RT Checked in Every Day?
• The Missing Piece Isn't Another Diet
• Eat the food you love. Stay accountable every day.
• One Bad Meal Doesn't Mean You Failed
women over 40 trying to lose weight

```html
<!DOCTYPE html>
<html lang="en">
<head>
<meta charset="utf-8">
<title>Quilvo Accountability Graphics</title>
<link rel="stylesheet" href="https://fonts.googleapis.com/css2?family=Fraunces:opsz,wght@9..144,800&family=Inter:wght@600;700&display=swap">
<style>
:root{
  --navy:#011b4f;
  --plum:#2c1843;
  --pink:#e23a72;
  --rose:#e04a7c;
  --beige:#ecdccb;
  --stone:#e5e3df;
  --paper:#ececec;
  --white:#ffffff;
  --mauve:#5d4566;
  --photo-warm:#b99a86;
  --photo-dark:#2a2533;
}
*{box-sizing:border-box;margin:0;padding:0}
html,body{width:1200px;height:582px;overflow:hidden;background:var(--navy)}
.board{position:relative;width:1200px;height:582px}
.card{position:absolute;width:185px;height:230px;border:3px solid var(--white);overflow:hidden;font-family:"Inter",sans-serif}
.headline{position:absolute;z-index:2;font-family:"Fraunces",serif;font-weight:800;color:var(--plum);line-height:.98;letter-spacing:-.2px}
.accent{color:var(--pink)}
.sub{position:absolute;z-index:2;font-size:6.4px;font-weight:700;color:var(--plum);line-height:1.25}
.dash{position:absolute;z-index:2;width:13px;height:1.5px;background:var(--pink)}
.brand{position:absolute;z-index:2;left:10px;bottom:7px;font-size:3.6px;font-weight:600;color:var(--plum);opacity:.6;letter-spacing:.2px}
.photo{position:absolute;z-index:1}
.center{text-align:center;left:0;right:0}
</style>
</head>
<body>
<div class="board">

  <div class="card" style="left:47px;top:39px;background:var(--beige)">
    <div class="photo" role="img" aria-label="Coach standing in black outfit, hand on hip" style="left:103px;top:68px;width:70px;height:162px;border-radius:35px 35px 0 0;background:linear-gradient(180deg,var(--photo-dark),#1b1a22)"></div>
    <div class="headline" style="left:11px;top:20px;font-size:20.5px">Stop<br>Starting Over<br>Every<br><span class="accent">Monday</span></div>
    <div class="dash" style="left:11px;top:118px"></div>
    <div class="sub" style="left:11px;top:128px;width:90px">Stay Consistent with RT in Your Pocket!</div>
    <div class="brand">QUILVO</div>
  </div>

  <div class="card" style="left:276px;top:39px;background:var(--stone)">
    <div class="headline" style="left:19px;top:15px;font-size:15.5px">You don't need<br>more willpower.<br><span class="accent">You need more<br>support.</span></div>
    <div class="photo" role="img" aria-label="Coach hugging a laughing client" style="left:62px;top:93px;width:72px;height:97px;border:2px solid var(--white);transform:rotate(1deg);background:linear-gradient(135deg,#7c5a5a,#e26a9e 60%,#c9d9a0)"></div>
    <div class="sub center" style="top:199px">Stay Consistent with RT in Your Pocket!</div>
    <div class="brand">QUILVO</div>
  </div>

  <div class="card" style="left:511px;top:39px;background:var(--beige)">
    <div class="photo" role="img" aria-label="Coach and client standing together laughing" style="left:0;top:0;width:185px;height:120px;background:linear-gradient(180deg,#d8c6b3,var(--photo-warm) 55%,#3a4666)"></div>
    <svg style="position:absolute;z-index:1;left:0;top:75px" width="185" height="60" viewBox="0 0 185 60"><path d="M0 20 C40 70 90 30 120 15 C140 6 160 5 185 8 L185 60 L0 60 Z" fill="var(--beige)"/><path d="M8 30 C45 72 95 28 125 14 C145 6 160 6 165 7" fill="none" stroke="#8a8a8a" stroke-width="3"/></svg>
    <div class="headline center accent" style="top:127px;font-size:16.5px">Built for women<br>who are tired of<br>doing this <span style="color:var(--plum)">alone</span></div>
    <div class="dash" style="left:86px;top:183px"></div>
    <div class="sub center" style="top:191px">Stay Consistent with RT in Your Pocket!</div>
    <div class="brand">QUILVO</div>
  </div>

  <div class="card" style="left:747px;top:39px;background:var(--rose)">
    <div class="headline" style="left:10px;top:13px;font-size:16.5px;color:var(--white)">When Motivation<br>Fades,<br><span style="color:var(--plum)">RT Checks In.</span></div>
    <div class="dash" style="left:11px;top:72px;background:var(--plum)"></div>
    <div class="sub" style="left:11px;top:81px;font-size:4.6px;color:var(--white);width:60px">Stay Consistent with RT in Your Pocket!</div>
    <div style="position:absolute;left:50px;top:113px;width:88px;height:117px;border-radius:18px 18px 0 0;background:linear-gradient(180deg,rgba(255,255,255,.35),rgba(255,255,255,.75))"></div>
    <div class="photo" role="img" aria-label="Coach standing in black outfit, hand on hip" style="left:62px;top:76px;width:64px;height:154px;border-radius:32px 32px 0 0;background:linear-gradient(180deg,var(--photo-dark),#1b1a22)"></div>
    <div class="brand" style="color:var(--white)">QUILVO</div>
  </div>

  <div class="card" style="left:976px;top:39px">
    <div class="photo" role="img" aria-label="Coach hugging a laughing client" style="inset:0;background:linear-gradient(180deg,#a77a8e,#d6609a 55%,#e0447a)"></div>
    <div class="headline center" style="top:124px;font-size:16px;color:var(--white)">The Support System<br>You've Been <span style="color:var(--plum)">Missing</span></div>
    <div class="dash" style="left:86px;top:166px;background:var(--white)"></div>
    <div class="sub center" style="top:176px">Stay Consistent with RT in Your Pocket!</div>
    <div class="brand">QUILVO</div>
  </div>

  <div class="card" style="left:47px;top:311px;background:var(--white)">
    <div class="photo" role="img" aria-label="Coach and client standing together laughing" style="left:0;top:0;width:185px;height:115px;background:linear-gradient(180deg,#d8c6b3,var(--photo-warm) 45%,var(--white))"></div>
    <div class="headline center" style="top:108px;font-size:17px;line-height:1.3">Support When<br>Motivation<br><span class="accent">Disappears</span></div>
    <div class="dash" style="left:86px;top:179px"></div>
    <div class="sub center" style="top:190px">Stay Consistent with RT in Your Pocket!</div>
    <div class="brand">QUILVO</div>
  </div>

  <div class="card" style="left:276px;top:311px;background:var(--paper)">
    <div class="photo" role="img" aria-label="Coach standing in black outfit, hand on hip" style="left:50px;top:74px;width:66px;height:156px;border-radius:33px 33px 0 0;background:linear-gradient(180deg,var(--photo-dark),#1b1a22)"></div>
    <div class="headline center" style="top:16px;font-size:22px;line-height:.95">What if RT<br>Checked in<br><span class="accent">Every Day?</span></div>
    <div class="sub" style="left:122px;top:170px;font-size:6.6px">Stay<br>Consistent<br>with RT in<br>Your Pocket!</div>
    <div class="brand">QUILVO</div>
  </div>

  <div class="card" style="left:511px;top:311px;background:var(--mauve)">
    <div class="headline" style="left:9px;top:13px;font-size:17.5px;color:var(--white)">The Missing Piece<br>Isn't Another Diet</div>
    <div class="dash" style="left:77px;top:63px"></div>
    <div class="sub center" style="top:76px;color:var(--pink)">Stay Consistent with RT in Your Pocket!</div>
    <div class="photo" role="img" aria-label="Coach hugging a laughing client" style="left:0;top:112px;width:185px;height:118px;background:linear-gradient(135deg,#c98cb0,#d462a0 55%,#ead3ea)"></div>
    <svg style="position:absolute;z-index:1;left:0;top:104px" width="185" height="16" viewBox="0 0 185 16"><path d="M0 6 L12 4 L22 8 L35 3 L50 7 L64 2 L80 6 L96 3 L110 7 L126 2 L142 6 L158 3 L172 7 L185 4 L185 12 L170 14 L150 10 L132 15 L112 11 L92 15 L72 11 L52 15 L32 11 L14 15 L0 12 Z" fill="#f4f2f2"/></svg>
    <div class="brand" style="color:var(--white)">QUILVO</div>
  </div>

  <div class="card" style="left:747px;top:311px">
    <div class="photo" role="img" aria-label="Coach standing in a lounge with a pool table" style="inset:0;background:linear-gradient(180deg,#5a5468,#4e3e56 55%,#3a3446)"></div>
    <div class="headline" style="left:14px;top:68px;font-size:17px;color:var(--white);line-height:1.08">Eat the food<br>you love.<br>Stay <span class="accent">accountable</span><br>every day.</div>
    <div class="dash" style="left:15px;top:150px"></div>
    <div class="sub" style="left:15px;top:160px;color:var(--white)">Stay Consistent with RT in Your Pocket!</div>
    <div class="brand" style="color:var(--white)">QUILVO</div>
  </div>

  <div class="card" style="left:976px;top:311px;background:#f6f6f7">
    <div class="photo" role="img" aria-label="Coach and client standing together laughing" style="left:0;top:0;width:185px;height:138px;background:linear-gradient(180deg,#d8c6b3,var(--photo-warm) 50%,#3a4666)"></div>
    <div style="position:absolute;z-index:1;left:19px;top:104px;width:145px;height:74px;background:var(--white)"></div>
    <div class="headline center" style="top:113px;font-size:17px">One Bad Meal<br>Doesn't Mean<br>You <span class="accent">Failed</span></div>
    <div class="sub center" style="top:189px">Stay Consistent with RT in Your Pocket!</div>
    <div class="brand">QUILVO</div>
  </div>

</div>
</body>
</html>
```